Goat's Milk Soap

International product development company seeking designs for the following soap label:

Hand crafted in Mt Ellerby QLD Australia, Ashgrove Valley
Second Generation Goat Farmers
Soap is hand made in appearance but gives an instant soothing feel when used
High in Vegetable oils and pure fresh goats milk (no powders used)
Give the emotional feel of Quality and Hand crafted
Label must stimulate an emotional response visually
Label must deliver to the customer anticipation for use.
Would anticipate that the label will be produced on a matte finish brown paper label or similar.

Logo should be no larger than 50mm x 50mm
Label should measure around 120mm x 70mm

It Company

```html
<!DOCTYPE html>
<html lang="en">
<head>
<meta charset="utf-8">
<title>Goat's Milk Soap – Label Option 1</title>
<link rel="stylesheet" href="https://fonts.googleapis.com/css2?family=Nunito:wght@900&family=Source+Sans+3:wght@400&display=swap">
<style>
  :root {
    --page: #ffffff;
    --label-teal: #85cbd1;
    --tab-gold: #f9b51f;
    --badge-brown: #332b2c;
    --badge-edge: #f3a51e;
    --badge-inner-line: #8a8080;
    --ink: #1a1a1a;
    --title-teal: #85cbd1;
  }
  html, body {
    margin: 0;
    padding: 0;
    overflow: hidden;
    background: var(--page);
  }
  .canvas {
    position: relative;
    width: 697px;
    height: 1200px;
    overflow: hidden;
    background: var(--page);
    font-family: "Source Sans 3", "Myriad Pro", sans-serif;
    color: var(--ink);
  }
  .spec-width {
    position: absolute;
    top: 0;
    left: 173px;
    width: 300px;
    text-align: center;
    font-size: 33px;
    line-height: 40px;
  }
  .spec-height {
    position: absolute;
    left: 672px;
    top: 645px;
    font-size: 33px;
    transform: translate(-50%, -50%) rotate(90deg);
    white-space: nowrap;
  }
  .label-art {
    position: absolute;
    left: 0;
    top: 0;
  }
  .product-title {
    position: absolute;
    left: 112px;
    width: 400px;
    top: 440px;
    margin: 0;
    text-align: center;
    font-family: "Nunito", "Arial Rounded MT Bold", sans-serif;
    font-weight: 900;
    font-size: 64px;
    line-height: 70px;
    letter-spacing: 1px;
    color: var(--title-teal);
    text-transform: uppercase;
  }
  .origin-line {
    position: absolute;
    left: 0;
    width: 646px;
    top: 898px;
    margin: 0;
    text-align: center;
    font-size: 28px;
    line-height: 36px;
  }
</style>
</head>
<body>
<div class="canvas">
  <div class="spec-width">Option 1<br>70mm</div>
  <div class="spec-height">120mm</div>

  <svg class="label-art" width="697" height="1200" viewBox="0 0 697 1200" aria-hidden="false">
    <defs>
      <radialGradient id="tab-glow" cx="50%" cy="50%" r="50%">
        <stop offset="0" stop-color="#ffffff" stop-opacity="0.9"/>
        <stop offset="1" stop-color="#ffffff" stop-opacity="0"/>
      </radialGradient>
      <linearGradient id="tab-shade-top" x1="0" y1="0" x2="0" y2="1">
        <stop offset="0.6" stop-color="#000" stop-opacity="0"/>
        <stop offset="1" stop-color="#000" stop-opacity="0.25"/>
      </linearGradient>
      <linearGradient id="tab-shade-bottom" x1="0" y1="1" x2="0" y2="0">
        <stop offset="0.75" stop-color="#000" stop-opacity="0"/>
        <stop offset="1" stop-color="#000" stop-opacity="0.25"/>
      </linearGradient>
    </defs>

    <!-- label body -->
    <rect class="label-body" x="2" y="92" width="646" height="1110" fill="var(--label-teal)" stroke="#222" stroke-width="1"/>

    <!-- top tab -->
    <g class="tab tab-top">
      <rect x="200" y="92" width="247" height="186" fill="var(--tab-gold)"/>
      <rect x="200" y="92" width="247" height="186" fill="url(#tab-shade-top)"/>
      <line x1="212" y1="92" x2="212" y2="272" stroke="#fff" stroke-width="2"/>
      <line x1="435" y1="92" x2="435" y2="272" stroke="#fff" stroke-width="2"/>
      <circle cx="323" cy="190" r="72" fill="var(--label-teal)" role="img" aria-label="Goat head emblem"/>
      <ellipse cx="323" cy="283" rx="190" ry="5" fill="url(#tab-glow)"/>
    </g>

    <!-- bottom tab -->
    <g class="tab tab-bottom">
      <rect x="200" y="995" width="247" height="207" fill="var(--tab-gold)"/>
      <rect x="200" y="995" width="247" height="207" fill="url(#tab-shade-bottom)"/>
      <line x1="212" y1="1002" x2="212" y2="1200" stroke="#fff" stroke-width="2"/>
      <line x1="435" y1="1002" x2="435" y2="1200" stroke="#fff" stroke-width="2"/>
      <circle cx="323" cy="1090" r="72" fill="var(--label-teal)" role="img" aria-label="Goat head emblem"/>
      <ellipse cx="323" cy="993" rx="190" ry="5" fill="url(#tab-glow)"/>
    </g>

    <!-- title badge -->
    <g class="title-badge">
      <path d="M150,372 C200,372 230,335 312,335 C394,335 424,372 474,372 Q474,402 504,402 L504,440 C552,450 552,535 504,545 L504,585 Q474,585 474,615 C424,615 394,655 312,655 C230,655 200,615 150,615 Q150,585 120,585 L120,545 C72,535 72,450 120,440 L120,402 Q150,402 150,372 Z"
            fill="var(--badge-brown)" stroke="var(--badge-edge)" stroke-width="4"/>
      <path transform="translate(312 495) scale(0.88) translate(-312 -495)"
            d="M150,372 C200,372 230,335 312,335 C394,335 424,372 474,372 Q474,402 504,402 L504,440 C552,450 552,535 504,545 L504,585 Q474,585 474,615 C424,615 394,655 312,655 C230,655 200,615 150,615 Q150,585 120,585 L120,545 C72,535 72,450 120,440 L120,402 Q150,402 150,372 Z"
            fill="none" stroke="var(--badge-inner-line)" stroke-width="2.5"/>
      <rect x="252" y="404" width="120" height="14" rx="7" fill="var(--badge-edge)" role="img" aria-label="Scroll flourish"/>
      <rect x="252" y="592" width="120" height="14" rx="7" fill="var(--badge-edge)" role="img" aria-label="Scroll flourish"/>
    </g>
  </svg>

  <h1 class="product-title">Goat’s<br>Milk Soap</h1>

  <p class="origin-line">Hand crafted in Mt Ellerby<br>QLD Australia, Ashgrove Valley</p>
</div>
</body>
</html>
```